Web Developer Needs a Business Card Design

I need a personal business card design that represents me as a web developer for potential employers. I would like the background to be a dark color on the front for contrast with my logo and name. The back will have all my information along with a smaller version of the logo. I want something with a modern look and feel, not too conservative. This will be used for potential employers and freelance work.

Industry/Entity Type

Business

Contact Information for Business Card

Front should have my logo and name. The back should have all my personal information which would include: name: Tom Varulek, phone: 570-614-3098, email: tomvarulek@quillbox.net, website url: www.tomvarulek.net, logo, web developer.

Font styles to use
Sans Serif

Requirements
Must have
• Must include my logo. The color palette base color will be the logo color.

```html
<!DOCTYPE html>
<html lang="en">
<head>
<meta charset="utf-8">
<title>Tom Varulek – Business Card</title>
<link rel="stylesheet" href="https://fonts.googleapis.com/css2?family=Open+Sans:wght@400;600;700&display=swap">
<style>
  :root {
    --teal: #6cc9b4;
    --teal-deep: #4fb39d;
    --ink: #0a0a0a;
    --paper: #ffffff;
    --text-dark: #1d1d1d;
    --silver: #c9c9c9;
    --stage: #ebe8e4;
  }
  * { margin: 0; padding: 0; box-sizing: border-box; }
  html, body { width: 1200px; height: 913px; overflow: hidden; }
  body {
    background: var(--stage);
    font-family: "Open Sans", sans-serif;
    position: relative;
  }
  .card {
    position: absolute;
    width: 500px;
    height: 286px;
    border-radius: 18px;
    overflow: hidden;
    box-shadow: 0 10px 30px rgba(0,0,0,.18);
  }
  .card-front { left: 70px; top: 314px; background: var(--ink); }
  .card-back  { left: 630px; top: 314px; background: var(--paper); }
  .swoosh { position: absolute; inset: 0; width: 100%; height: 100%; }

  .mark {
    position: absolute;
    border-radius: 50%;
    border: solid var(--teal);
    display: flex;
    align-items: center;
    justify-content: center;
    color: var(--teal);
    font-weight: 700;
    text-align: center;
  }
  .card-front .mark {
    left: 48px; top: 52px; width: 164px; height: 164px;
    border-width: 16px; font-size: 17px; line-height: 1.2;
  }
  .divider {
    position: absolute; left: 250px; top: 40px;
    width: 1px; height: 120px;
    background: linear-gradient(var(--silver), rgba(201,201,201,.2));
  }
  .contact { position: absolute; left: 272px; top: 44px; color: var(--paper); }
  .contact-name { font-size: 21px; font-weight: 700; letter-spacing: .5px; text-transform: uppercase; line-height: 1.1; }
  .contact-role { font-size: 12px; font-weight: 700; color: var(--teal); letter-spacing: .8px; text-transform: uppercase; margin-bottom: 10px; }
  .contact-list { list-style: none; font-size: 13.5px; line-height: 1.5; }
  .contact-list li { display: flex; align-items: center; gap: 8px; }
  .contact-list svg { width: 11px; height: 11px; flex: none; }

  .card-back .mark {
    left: 210px; top: 32px; width: 80px; height: 80px;
    border-width: 7px; font-size: 10px; line-height: 1.15;
  }
  .back-name {
    position: absolute; left: 0; right: 0; top: 128px; text-align: center;
    font-size: 31px; font-weight: 400; letter-spacing: 2px; color: var(--text-dark);
    text-transform: uppercase;
  }
  .back-role {
    position: absolute; left: 0; right: 0; top: 172px; text-align: center;
    font-size: 16px; color: var(--text-dark); letter-spacing: .5px;
  }
</style>
</head>
<body>

<section class="card card-front" aria-label="Business card front">
  <svg class="swoosh" viewBox="0 0 500 286" preserveAspectRatio="none" aria-hidden="true">
    <defs>
      <linearGradient id="chrome-dark" x1="0" x2="1">
        <stop offset="0" stop-color="#444"/><stop offset=".5" stop-color="#fff"/><stop offset="1" stop-color="#777"/>
      </linearGradient>
    </defs>
    <path d="M90 286 Q330 250 500 130 L500 142 Q340 262 130 286 Z" fill="url(#chrome-dark)"/>
    <path d="M130 286 Q340 262 500 142 L500 286 Z" fill="var(--teal)"/>
  </svg>
  <div class="mark">Tom<br>Varulek</div>
  <div class="divider"></div>
  <div class="contact">
    <p class="contact-name">Tom Varulek</p>
    <p class="contact-role">Web Developer</p>
    <ul class="contact-list">
      <li><svg viewBox="0 0 12 12"><path d="M2 1h2.5l1 3-1.5 1a7 7 0 0 0 3 3l1-1.5 3 1V11a1 1 0 0 1-1 1A10 10 0 0 1 1 2a1 1 0 0 1 1-1z" fill="var(--teal)"/></svg>570-614-3098</li>
      <li><svg viewBox="0 0 12 12"><rect x="1" y="2.5" width="10" height="7" fill="none" stroke="var(--teal)" stroke-width="1.3"/><path d="M1 2.5l5 4 5-4" fill="none" stroke="var(--teal)" stroke-width="1.3"/></svg>tomvarulek@quillbox.net</li>
      <li><svg viewBox="0 0 12 12"><circle cx="6" cy="6" r="5" fill="none" stroke="var(--teal)" stroke-width="1.3"/><path d="M1 6h10M6 1c-3 3-3 7 0 10M6 1c3 3 3 7 0 10" fill="none" stroke="var(--teal)" stroke-width="1"/></svg>www.tomvarulek.net</li>
    </ul>
  </div>
</section>

<section class="card card-back" aria-label="Business card back">
  <svg class="swoosh" viewBox="0 0 500 286" preserveAspectRatio="none" aria-hidden="true">
    <defs>
      <linearGradient id="chrome-light" x1="0" x2="1">
        <stop offset="0" stop-color="#fff"/><stop offset=".5" stop-color="#111"/><stop offset="1" stop-color="#bbb"/>
      </linearGradient>
    </defs>
    <path d="M70 286 Q330 255 500 150 L500 160 Q340 268 110 286 Z" fill="url(#chrome-light)"/>
    <path d="M110 286 Q340 268 500 160 L500 286 Z" fill="var(--teal)"/>
  </svg>
  <div class="mark">Tom<br>Varulek</div>
  <p class="back-name">Tom Varulek</p>
  <p class="back-role">Front-End Developer</p>
</section>

</body>
</html>
```